Brindlewick Solutions Ltd

I'd like to create a company letterhead for the attached logo in word format.

I'd like to emphasis the icon in large translucent state from the left corner and ensure that the letterhead colouring matches the colour palette of the current logo with a contrast so it's clear to see. I've attached a copy of our sister company page on the app for reference.

```html
<!DOCTYPE html>
<html lang="en">
<head>
<meta charset="utf-8">
<title>Brindlewick Solutions Ltd – Letterhead</title>
<link href="https://fonts.googleapis.com/css2?family=Arimo:wght@400&family=Mulish:wght@700;800&family=Encode+Sans+Condensed:wght@400&display=swap" rel="stylesheet">
<style>
  :root {
    --teal: #00b9a4;
    --teal-tint: #eef8f8;
    --rule-grey: #9a9a9a;
    --ink: #555555;
    --ink-soft: #8f8f8f;
    --backdrop: #e2e2e2;
    --paper: #ffffff;
  }
  * { margin: 0; padding: 0; box-sizing: border-box; }
  html, body {
    width: 1200px; height: 1200px; overflow: hidden;
    background: var(--backdrop);
  }
  .letterhead {
    position: absolute; left: 204px; top: 40px;
    width: 792px; height: 1120px;
    background: var(--paper);
    overflow: hidden;
    font-family: "Arimo", Arial, sans-serif;
    color: var(--ink);
  }
  .watermark-disc {
    position: absolute; left: -300px; top: 240px;
    width: 840px; height: 840px; border-radius: 50%;
    background: var(--teal-tint);
  }
  .band-teal {
    position: absolute; top: 112px; height: 7px; background: var(--teal);
  }
  .band-teal.left { left: 0; width: 66px; }
  .band-teal.right { left: 340px; right: 0; }
  .band-grey {
    position: absolute; top: 126px; left: 0; right: 0; height: 2px;
    background: var(--rule-grey);
  }
  .brand {
    position: absolute; left: 72px; top: 86px;
    display: flex; align-items: center; gap: 10px;
  }
  .brand-dot {
    width: 26px; height: 26px; border-radius: 50%; background: var(--teal);
  }
  .brand-name {
    font-family: "Mulish", sans-serif; font-weight: 700;
    font-size: 20px; color: var(--teal); letter-spacing: 0.2px;
    white-space: nowrap;
  }
  .contact {
    position: absolute; top: 50px; left: 0; right: 0; height: 60px;
    font-size: 12px; line-height: 18px; color: var(--ink-soft);
  }
  .contact-address {
    position: absolute; right: 236px; top: 0; text-align: right;
  }
  .contact-divider {
    position: absolute; left: 569px; top: 2px; width: 1px; height: 46px;
    background: var(--rule-grey);
  }
  .contact-lines {
    position: absolute; left: 580px; top: 0; list-style: none;
  }
  .contact-lines li { display: flex; align-items: center; gap: 7px; }
  .contact-lines svg { width: 11px; height: 11px; fill: var(--teal); }
  .letter {
    position: absolute; left: 71px; top: 425px; width: 648px;
  }
  .salutation {
    font-family: "Mulish", sans-serif; font-weight: 800;
    font-size: 18.5px; margin-left: 1px; margin-bottom: 24px;
  }
  .letter p {
    font-size: 13.3px; line-height: 16.2px; margin-bottom: 14px;
  }
  .closing {
    font-family: "Mulish", sans-serif; font-weight: 800;
    font-size: 10.5px; margin: 34px 0 0 1px;
  }
  .signature {
    font-family: "Encode Sans Condensed", sans-serif;
    font-size: 19px; letter-spacing: -0.9px; margin: 28px 0 0 21px;
  }
</style>
</head>
<body>
<main class="letterhead">
  <div class="watermark-disc" role="img" aria-label="Large faint brand decoration"></div>

  <div class="band-teal left"></div>
  <div class="band-teal right"></div>
  <div class="band-grey"></div>

  <div class="brand">
    <span class="brand-dot"></span>
    <span class="brand-name">Brindlewick Solutions Ltd</span>
  </div>

  <div class="contact">
    <address class="contact-address" style="font-style:normal">
      Your address<br>city<br>state, ZIP 0000
    </address>
    <div class="contact-divider"></div>
    <ul class="contact-lines">
      <li>
        <svg viewBox="0 0 24 24" aria-hidden="true"><path d="M6.6 10.8a15.1 15.1 0 0 0 6.6 6.6l2.2-2.2c.3-.3.7-.4 1-.2 1.1.4 2.3.6 3.6.6.6 0 1 .4 1 1V20c0 .6-.4 1-1 1A17 17 0 0 1 3 4c0-.6.4-1 1-1h3.5c.6 0 1 .4 1 1 0 1.3.2 2.5.6 3.6.1.3 0 .7-.2 1z"/></svg>
        555-014-2738
      </li>
      <li>
        <svg viewBox="0 0 24 24" aria-hidden="true"><path d="M2 5h20v14H2zm2 2v.4l8 5.2 8-5.2V7zm0 2.8V17h16V9.8l-8 5.2z"/></svg>
        hello@brindlewick-mail.com
      </li>
      <li>
        <svg viewBox="0 0 24 24" aria-hidden="true"><path d="M12 2a10 10 0 1 0 0 20 10 10 0 0 0 0-20zm6.9 6h-3a15.6 15.6 0 0 0-1.3-3.9A8 8 0 0 1 18.9 8zM12 4c.8 1.2 1.5 2.5 1.9 4h-3.8c.4-1.5 1.1-2.8 1.9-4zM4.3 14a8 8 0 0 1 0-4h3.4a16 16 0 0 0 0 4zm.8 2h3a15.6 15.6 0 0 0 1.3 3.9A8 8 0 0 1 5.1 16zm3-8h-3a8 8 0 0 1 4.3-3.9C8.8 5.3 8.4 6.6 8.1 8zM12 20c-.8-1.2-1.5-2.5-1.9-4h3.8c-.4 1.5-1.1 2.8-1.9 4zm2.3-6H9.7a14.7 14.7 0 0 1 0-4h4.6a14.7 14.7 0 0 1 0 4zm.3 5.9c.6-1.2 1-2.5 1.3-3.9h3a8 8 0 0 1-4.3 3.9zm1.7-5.9a16 16 0 0 0 0-4h3.4a8 8 0 0 1 0 4z"/></svg>
        www.brindlewick-example.com
      </li>
    </ul>
  </div>

  <article class="letter">
    <h1 class="salutation">Dear Mr. Harlow,</h1>
    <p>Lorem ipsum dolor sit amet, consectetuer adipiscing elit, sed diam nonmmy nibh euismod tincidunt ut laor eet dolore magna aliquam erat volutpat. Ut wisi enim ad minim veniam, quis nostrud exerci tationmcorper suscipit lobortis nisl ut aliquip ex ea commodo consequat. Duis autem vel eum iriure dolor in hendrerit in vulputate velit esse molestie consequat, vel illum dolore eu feugiat</p>
    <p>Rorem ipsum dolor sit amet, consectetuer adipiscing elit, sed diam nonmmy nibh euismod tincidunt ut laor eet dolore magna aliquam erat volutpat. Ut wisi enim ad minim veniam, quis nostrud exerci tationmcorper suscipit lobortis nisl ut aliquip ex ea commodo consequat. Duis autem vel eum iriure dolor in hendrerit in vulputate velit esse molest</p>
    <p>Dorem ipsum dolor sit amet, consectetuer adipiscing elit, sed diam nonmmy nibh euismod tincidunt ut laor eet dolore magna aliquam erat volutpat. Ut wisi enim ad minim veniam, quis nostrud exerci tationmcorper suscipit lobortis nisl ut aliquip ex ea commodo consequat. Duis autem vel eum iriure dolor in hendrerit in suscipit lobortis nisl ut aliquip ex ea commodo consequat. Duis autem vel eum iriure dolor in hendrerit in vulputate velit esse molestie consequat, vel illum</p>
    <p>Sorem ipsum dolor sit amet, consectetuer adipiscing elit, sed diam nonmmy nibh euismod tincidunt ut laor eet dolore magna aliquam erat volutpat. Ut wisi enim ad minim veniam, quis nostrud exerci tationmcorper suscipit lobortis nisl ut aliquip ex ea commodo consequat. Duis autem vel eum iriure dolor in</p>
    <div class="closing">Sincerely,</div>
    <div class="signature">Marin Coltrane</div>
  </article>
</main>
</body>
</html>
```